BOLD & MINIMALIST DESIGN NEEDED

We want a very bold but minimalistic business card design that is impactful and utilizes both sides of the business card. Our current logo is included for your use.

We want bold fonts and good use of negative space. We don't want the logo to overpower the design.

Target Market(s)

Professionals who are building new commercial buildings.

Industry/Entity Type

Construction

Contact Information for Business Card

Name, Title, email, office phone, cell phone, website

Font styles to use
Serif
Sans Serif

Requirements
Must have
• Bold design!

```html
<!DOCTYPE html>
<html lang="en">
<head>
<meta charset="utf-8">
<title>Ridgeline Design + Build — Business Card</title>
<link href="https://fonts.googleapis.com/css2?family=Arimo:wght@400;700&display=swap" rel="stylesheet">
<style>
  :root{
    --bg:#c4c4c4;
    --green-deep:#2f5410;
    --green-mid:#4d7d1b;
    --green-band:#6f9f24;
    --green-bright:#8cc63f;
    --ink:#0c0d10;
    --white:#ffffff;
  }
  *{box-sizing:border-box;margin:0;padding:0}
  html,body{width:1200px;height:802px;overflow:hidden}
  body{
    background:var(--bg);
    font-family:"Arimo",Arial,sans-serif;
    display:flex;align-items:center;justify-content:center;gap:40px;
  }
  .card{
    position:relative;width:540px;height:309px;border-radius:14px;overflow:hidden;
    box-shadow:0 10px 24px rgba(0,0,0,.28);
  }
  /* front */
  .card--front{background:radial-gradient(ellipse at 30% 35%,var(--green-mid),var(--green-deep) 90%)}
  .front__band{position:absolute;left:0;right:0;bottom:0;height:128px;background:var(--green-band)}
  .front__notch{position:absolute;left:0;bottom:128px;width:64px;height:12px;background:var(--green-band);
    clip-path:polygon(0 100%,0 0,70% 0,100% 100%)}
  .brand{position:absolute;right:34px;top:46px;display:flex;align-items:center;gap:10px;
    color:var(--white);font-weight:700;font-size:30px;letter-spacing:.5px}
  .brand__mark{width:14px;height:14px;background:var(--green-bright)}
  .brand__sub{position:absolute;right:34px;top:88px;color:var(--white);font-weight:700;font-size:12px;letter-spacing:5px}
  .person{position:absolute;left:30px;top:104px}
  .person__name{color:var(--green-bright);font-weight:700;font-size:27px;letter-spacing:.5px}
  .person__title{color:var(--white);font-size:17px;margin-top:6px}
  .contact{position:absolute;left:30px;bottom:22px;list-style:none;color:var(--white);font-size:15px;line-height:27px}
  .contact li{display:flex;align-items:center;gap:10px}
  .contact svg{width:15px;height:15px;fill:var(--white)}
  .office{position:absolute;right:30px;bottom:22px;text-align:right;color:var(--white);font-size:15px;line-height:24px}
  .office__web{margin-top:12px;display:flex;align-items:center;gap:10px;justify-content:flex-end}
  .office__web svg{width:15px;height:15px}
  /* back */
  .card--back{background:radial-gradient(ellipse at 25% 40%,var(--green-mid),var(--green-deep) 95%)}
  .back__monogram{position:absolute;right:0;top:0;width:300px;height:309px;
    background:linear-gradient(120deg,var(--ink) 0%,#1d2a10 50%,var(--green-bright) 100%);opacity:.9}
  .back__brand{position:absolute;left:36px;bottom:42px;color:var(--white)}
  .back__name{display:flex;align-items:center;gap:10px;font-weight:700;font-size:32px}
  .back__sub{margin-top:6px;font-weight:700;font-size:12px;letter-spacing:5px}
</style>
</head>
<body>
  <section class="card card--front" aria-label="Card front">
    <div class="front__band"></div>
    <div class="front__notch"></div>
    <div class="brand"><span class="brand__mark"></span>RIDGELINE</div>
    <div class="brand__sub">DESIGN + BUILD</div>
    <div class="person">
      <p class="person__name">MARCUS HALE</p>
      <p class="person__title">Founder &amp; CEO</p>
    </div>
    <ul class="contact">
      <li><svg viewBox="0 0 24 24"><path d="M6.6 10.8a15 15 0 0 0 6.6 6.6l2.2-2.2c.3-.3.7-.4 1-.2 1.1.4 2.3.6 3.6.6.6 0 1 .4 1 1V20c0 .6-.4 1-1 1A17 17 0 0 1 3 4c0-.6.4-1 1-1h3.5c.6 0 1 .4 1 1 0 1.3.2 2.5.6 3.6.1.3 0 .7-.2 1z"/></svg>015-482-730-216</li>
      <li><svg viewBox="0 0 24 24"><rect x="6" y="2" width="12" height="20" rx="2"/><rect x="8" y="4" width="8" height="13" fill="#6f9f24"/></svg>047-318-902-654</li>
      <li><svg viewBox="0 0 24 24"><path d="M2 12 22 3l-6 19-4-8z"/></svg>hello@ridgelinebuild.com</li>
    </ul>
    <div class="office">
      <p>4471 Cedar Bluff Pkwy</p>
      <p>210-B, FL 32561</p>
      <p class="office__web"><svg viewBox="0 0 24 24" fill="none" stroke="#fff" stroke-width="2"><circle cx="12" cy="12" r="9"/><path d="M3 12h18M12 3c3 3 3 15 0 18M12 3c-3 3-3 15 0 18"/></svg>www.ridgelinebuild.com</p>
    </div>
  </section>

  <section class="card card--back" aria-label="Card back">
    <div class="back__monogram" role="img" aria-label="Large brand monogram area"></div>
    <div class="back__brand">
      <p class="back__name"><span class="brand__mark"></span>RIDGELINE</p>
      <p class="back__sub">DESIGN + BUILD</p>
    </div>
  </section>
</body>
</html>
```